Moravel Aesthetic Doctor

I require an elegant, luxurious looking business card for my aesthetic business. I am a doctor and that will set me aside from competitors. I am planning to provide home and spa based treatments to clients with high expectations. I have attached my logo.

```html
<!DOCTYPE html>
<html lang="en">
<head>
<meta charset="utf-8">
<title>Moravel Aesthetic Doctor – Business Card</title>
<link href="https://fonts.googleapis.com/css2?family=Marcellus&family=Roboto:ital,wght@0,400;1,400&display=swap" rel="stylesheet">
<style>
  :root {
    --page-bg: #c4c5c7;
    --card-blue-top: #4ba6de;
    --card-blue-bottom: #0b5fa9;
    --band-grey: #8f9aa7;
    --card-white: #f6f6f5;
    --ink-dark: #2e2f33;
    --ink-blue: #3d93d2;
    --ink-white: #ffffff;
    --ink-soft: #e8f1f9;
  }
  * { margin: 0; padding: 0; box-sizing: border-box; }
  html, body { width: 1200px; height: 576px; overflow: hidden; }
  body {
    background: var(--page-bg);
    position: relative;
    font-family: "Roboto", Arial, sans-serif;
  }
  .card {
    position: absolute;
    top: 138px;
    border-radius: 10px;
    overflow: hidden;
  }
  /* Front */
  .card-front {
    left: 82px;
    width: 484px;
    height: 294px;
    background: linear-gradient(160deg, var(--card-blue-top) 0%, #2a84c8 45%, var(--card-blue-bottom) 100%);
  }
  .front-mark {
    position: absolute;
    left: 58px;
    top: 50px;
    width: 96px;
    height: 96px;
    border: 2px solid var(--ink-white);
    border-radius: 50%;
  }
  .front-name {
    position: absolute;
    left: 180px;
    top: 62px;
    font-family: "Marcellus", Georgia, serif;
    color: var(--ink-white);
    font-weight: 400;
    line-height: 1;
  }
  .front-name .name-main { display: block; font-size: 50px; letter-spacing: 1px; }
  .front-name .name-sub { display: block; font-size: 22px; letter-spacing: 1.2px; margin-top: 6px; }
  .services {
    position: absolute;
    left: 0; right: 0;
    top: 198px;
    text-align: center;
    color: var(--ink-soft);
    font-size: 13px;
    line-height: 18px;
  }
  .services .sep { margin: 0 8px; }
  .treatment-band {
    position: absolute;
    left: 0; right: 0;
    top: 245px;
    height: 23px;
    background: var(--band-grey);
    color: var(--ink-white);
    font-family: "Marcellus", Georgia, serif;
    font-size: 13px;
    letter-spacing: 1px;
    text-align: center;
    line-height: 23px;
  }
  /* Back */
  .card-back {
    left: 602px;
    width: 481px;
    height: 292px;
    background: var(--card-white);
  }
  .holder {
    position: absolute;
    left: 27px;
    top: 50px;
  }
  .holder-name { font-size: 19px; color: var(--ink-dark); line-height: 1.2; }
  .holder-letters { font-size: 10px; font-style: italic; color: var(--ink-blue); margin-top: 3px; }
  .holder-diploma { font-size: 13px; color: var(--ink-blue); margin-top: 6px; }
  .contacts {
    position: absolute;
    left: 32px;
    top: 187px;
    list-style: none;
    font-size: 12.5px;
    color: var(--ink-dark);
  }
  .contacts li { display: flex; align-items: center; height: 18.5px; }
  .contacts svg { width: 10px; height: 10px; margin-right: 6px; fill: var(--ink-blue); }
  .contacts .follow { margin-top: 4px; margin-left: -3px; }
  .social-dot {
    display: inline-block;
    width: 11px; height: 11px;
    border-radius: 50%;
    background: var(--ink-blue);
    margin-left: 4px;
  }
  .social-dot:first-of-type { margin-left: 7px; }
  .back-mark {
    position: absolute;
    left: 224px;
    top: 190px;
    width: 72px;
    height: 72px;
    border: 2px solid var(--ink-blue);
    border-radius: 50%;
  }
  .back-name {
    position: absolute;
    left: 309px;
    top: 200px;
    font-family: "Marcellus", Georgia, serif;
    color: var(--ink-blue);
    font-weight: 400;
    line-height: 1;
  }
  .back-name .name-main { display: block; font-size: 29px; letter-spacing: 0.5px; }
  .back-name .name-sub { display: block; font-size: 13.4px; letter-spacing: 0.6px; margin-top: 6px; }
</style>
</head>
<body>
  <section class="card card-front" aria-label="Card front">
    <div class="front-mark" aria-hidden="true"></div>
    <h1 class="front-name">
      <span class="name-main">MORAVEL</span>
      <span class="name-sub">AESTHETIC DOCTOR</span>
    </h1>
    <p class="services">
      Dermal Injectables<span class="sep">|</span>Plasma Facials<span class="sep">|</span>Microneedling<br>
      Skin Boosters<span class="sep">|</span>Excessive Sweating
    </p>
    <div class="treatment-band">HOME AND SPA BASED TREATMENTS</div>
  </section>

  <section class="card card-back" aria-label="Card back">
    <div class="holder">
      <p class="holder-name">Dr Elise Varrow</p>
      <p class="holder-letters">MRCPCH MD</p>
      <p class="holder-diploma">Australasian Diploma of Aesthetic Medicine</p>
    </div>
    <ul class="contacts">
      <li>
        <svg viewBox="0 0 10 10" aria-hidden="true"><path d="M2.1 0.5 L3.6 2.4 L2.8 3.5 Q3.8 5.6 6.3 7.1 L7.5 6.3 L9.5 7.8 L8.4 9.4 Q4.6 9.2 2 6.4 Q0.3 4.2 0.6 1.6 Z"/></svg>
        0800 555 018
      </li>
      <li>
        <svg viewBox="0 0 10 10" aria-hidden="true"><path d="M0.5 2 H9.5 V8.2 H0.5 Z M1.2 2.6 L5 5.4 L8.8 2.6 V3.4 L5 6.2 L1.2 3.4 Z" fill-rule="evenodd"/></svg>
        elise@moravel.co.nz
      </li>
      <li>
        <svg viewBox="0 0 10 10" aria-hidden="true"><path d="M5 0.5 A4.5 4.5 0 1 0 5.01 0.5 Z M5 1.3 A3.7 3.7 0 1 1 4.99 1.3 Z M4.6 1 H5.4 V9 H4.6 Z M1 4.6 H9 V5.4 H1 Z M5 1 Q2.4 5 5 9 Q7.6 5 5 1 Z M5 2.2 Q3.4 5 5 7.8 Q6.6 5 5 2.2 Z" fill-rule="evenodd"/></svg>
        www.moravel.co.nz
      </li>
      <li class="follow">Follow us on:<span class="social-dot" aria-label="Social page"></span><span class="social-dot" aria-label="Social page"></span></li>
    </ul>
    <div class="back-mark" aria-hidden="true"></div>
    <p class="back-name">
      <span class="name-main">MORAVEL</span>
      <span class="name-sub">AESTHETIC DOCTOR</span>
    </p>
  </section>
</body>
</html>
```